CoinHarbor.com Site Redesign

We are looking to redesign our CoinHarbor.com site. This site is focused on helping consumers make smart financial decisions. We provide reviews and articles in various categories.

We are looking for a responsive design to run on wordpress. We will also have adsense advertisements on our page and will want some ad spot space. We are thinking of two column design vs. single column.

Here is an example of what our competitors look like:
ShopperBeacon.org (mostly reviews vs. articles)
Homepage - https://www.shopperbeacon.example/
Category Review Listing - https://www.shopperbeacon.example/mortgage-refinance/best-mortgage-refinance
Individual Review - https://www.shopperbeacon.example/mortgage-refinance/c/loan-orchard-mortgage-refinance-review

- I like that the site is extremely clean. I like the fixed header in mobile

PilotGuide
Homepage - https://www.pilotguide.example/
Category Review Listing-https://www.pilotguide.example/auto_insurance/index.php
Individual Review- https://www.pilotguide.example/auto_insurance/drivora_review.php

Articles - https://www.pilotguide.example/blog/2017/11/20/going-on-a-holiday-road-trip-be-prepared-for-these-hazards/

What I Like? I like the two column layout in that it gives room for advertising.
What I Do NOT Like? The top navigation is a little cumbersome and old. Mobile view is not very good. Content seems a bit cluttered.

PennyMoth
Homepage - https://www.pennymoth.example
Category Review Listing - https://www.pennymoth.example/blog/insurance/best-car-insurance-companies/?trk=pm_gn1_4.0
Individual Review- https://www.pennymoth.example/blog/insurance/veloro-insurance-review/

What I Like? very clean. Like the use of white space and focus on bright color call to action buttons.
What I Do NOT Like? In mobile a lot of content is pushed below the fold because of the large image above the fold. Reviews are not well organized.

Target Market(s)

consumers interested in saving money and making smart financial decisions

Industry/Entity Type

Financial

Logo Text

CoinHarbor.com or CoinHarbor

Coding

Coded - Design and coding required

Number of Pages Required

5+ page

Font styles to use
Sans Serif

Colors

Designer to choose colors to be used in the design.

Requirements
Must have
• -responsive design
• -room for ad space in the right column
Nice to have
• -good use of white space
• -clean layouts
Should not have
• -clutter

```html
<!DOCTYPE html>
<html lang="en">
<head>
<meta charset="utf-8">
<title>CoinHarbor.com – Make smarter financial decisions</title>
<link href="https://fonts.googleapis.com/css2?family=Raleway:wght@500;600;700;800&family=Open+Sans:ital,wght@0,400;0,600;0,700;1,400&display=swap" rel="stylesheet">
<style>
:root{
  --navy:#0b3a8f;
  --nav-active:#1f73c6;
  --blue:#1a8ad4;
  --blue-mid:#1567d9;
  --blue-deep:#0b3d9a;
  --link:#1b5fb8;
  --ink:#2b2b2b;
  --muted:#666;
  --line:#e2e2e2;
  --grey-bg:#eceef1;
  --footer-bg:#edeff2;
  --star:#f2b01e;
}
*{box-sizing:border-box;margin:0;padding:0}
html,body{width:1200px;height:3629px;overflow:hidden}
body{font-family:"Open Sans",Arial,sans-serif;color:var(--ink);background:#fff;position:relative}
.abs{position:absolute}
h1,h2,h3,h4{font-family:"Raleway",Arial,sans-serif}

/* header */
.site-header{position:absolute;left:0;top:0;width:1200px;height:68px;background:#fff}
.brand{position:absolute;left:162px;top:18px;display:flex;align-items:center;gap:8px;font-family:"Raleway",sans-serif;font-weight:700;font-size:21px;color:var(--navy)}
.brand-mark{width:30px;height:30px;background:var(--navy);border-radius:3px}
.search{position:absolute;left:649px;top:15px;width:388px;height:38px;border:1px solid #bbb;border-radius:19px;font-size:13px;color:#666;padding:9px 18px}
.search svg{position:absolute;right:16px;top:11px}

.main-nav{position:absolute;left:0;top:68px;width:1200px;height:53px;background:var(--navy)}
.main-nav ul{list-style:none;display:flex;position:absolute;left:162px;top:0;height:53px}
.main-nav li{font-family:"Raleway",sans-serif;font-weight:700;font-size:12px;color:#fff;letter-spacing:.5px;line-height:53px;padding:0 0}
.main-nav li.active{background:var(--nav-active)}

/* hero */
.hero{position:absolute;left:0;top:121px;width:1200px;height:421px;background:linear-gradient(120deg,#1b2d4f 0%,#3a5580 45%,#24385d 70%,#101c33 100%)}
.hero h1{position:absolute;top:140px;width:100%;text-align:center;color:#fff;font-size:40px;font-weight:700}
.hero .tagline{position:absolute;top:198px;width:100%;text-align:center;color:#fff;font-family:"Raleway",sans-serif;font-weight:700;font-size:21px;letter-spacing:.5px}
.hero .disclosure{position:absolute;top:357px;width:100%;text-align:center;color:#fff;font-size:15px}
.hero-arrow{position:absolute;top:195px;width:32px;height:32px;border:1.5px solid #fff;border-radius:50%}

/* categories */
.finder{position:absolute;left:162px;top:583px;width:603px;height:41px;background:#eaeaea;border-radius:20px;text-align:center;line-height:41px;font-size:14px;color:#333}
.finder b{font-weight:600}
.finder span{color:#777}
.category-grid{position:absolute;left:162px;top:644px;width:603px;display:grid;grid-template-columns:repeat(3,191px);column-gap:15px;row-gap:14px}
.category{height:160px;border:1px solid var(--line);background:#fff}
.category .thumb{height:116px}
.category p{font-size:13px;color:#222;padding:12px 8px 0}
.ad-column .ad{position:absolute;left:796px;width:242px}
.ad-brand{display:flex;align-items:center;justify-content:center;text-align:center;color:#fff;font-family:"Raleway",sans-serif;font-weight:800;font-size:25px;line-height:1.2}

.divider{position:absolute;left:0;top:1544px;width:1200px;height:1px;background:var(--line)}

/* about */
.about h2{position:absolute;top:1578px;width:1200px;text-align:center;font-size:29px;font-weight:700;color:#333}
.about .sub{position:absolute;top:1622px;width:1200px;text-align:center;font-family:"Raleway",sans-serif;font-size:16px;font-weight:600;color:#888}
.features{position:absolute;left:162px;top:1677px;width:876px;height:242px;display:flex}
.feature{flex:1;color:#fff;text-align:center;padding-top:30px}
.feature h3{font-size:16px;font-weight:700;margin-top:18px}
.feature p{font-size:13px;line-height:20px;margin:16px auto 0;width:200px}
.f1{background:var(--blue)}.f2{background:var(--blue-mid)}.f3{background:var(--blue-deep)}

/* reviews */
.reviews{position:absolute;left:0;top:1980px;width:1200px;height:380px;background:var(--grey-bg)}
.reviews .notch{position:absolute;left:570px;top:0}
.reviews h2{position:absolute;top:70px;width:100%;text-align:center;font-size:29px;font-weight:700;color:#333}
.avatar{position:absolute;left:266px;top:147px;width:126px;height:126px;border-radius:50%;background:linear-gradient(160deg,#c8ccd2,#7d8590)}
.quote{position:absolute;left:424px;top:150px;width:532px;font-style:italic;font-size:12.5px;line-height:22px;color:#444}
.reviewer{position:absolute;left:424px;top:255px;font-size:13px;font-weight:700;color:var(--link)}
.stars{position:absolute;left:424px;top:282px;color:var(--star);font-size:15px;letter-spacing:1px}
.slide-btn{position:absolute;top:160px;width:58px;height:58px;border-radius:50%;background:#e3e5e8;border:1px solid #d6d8db}
.slide-btn svg{position:absolute;left:22px;top:21px}

/* articles */
.articles h2{position:absolute;top:2406px;width:1200px;text-align:center;font-size:29px;font-weight:700;color:#333}
.article{position:absolute;width:276px}
.article .thumb{height:150px}
.article h3{font-size:16px;font-weight:600;color:var(--link);line-height:21px;margin-top:14px}
.article p{font-size:11.5px;line-height:18px;color:#333;margin-top:10px}
.article a{display:block;font-size:12px;font-weight:700;color:var(--link);text-decoration:none;margin-top:10px}

/* footer */
.site-footer{position:absolute;left:0;top:3195px;width:1200px;height:434px;background:var(--footer-bg)}
.site-footer h4{font-size:13px;font-weight:700;color:var(--link);position:absolute;top:50px}
.site-footer ul{list-style:none;position:absolute;top:86px;font-size:11px;line-height:20px;color:#333}
.news-text{position:absolute;left:766px;top:86px;width:272px;font-size:11px;line-height:20px;color:#333}
.email{position:absolute;left:766px;top:130px;width:272px;height:36px;background:#fff;border:1px solid #ccc;font-size:11px;padding:10px 8px;color:#333}
.signup{position:absolute;left:766px;top:180px;width:84px;height:36px;background:#1670b5;color:#fff;font-size:12px;font-weight:700;text-align:center;line-height:36px}
.footer-rule{position:absolute;left:162px;top:284px;width:876px;height:1px;background:#d8dadd}
.copyright{position:absolute;left:162px;top:300px;font-size:11px;color:#333}
.social{position:absolute;left:906px;top:296px;display:flex;gap:6px}
.social span{width:26px;height:26px;border-radius:50%;border:2px solid #333;background:#fff}
.footer-rule2{position:absolute;left:162px;top:350px;width:876px;height:1px;background:#d8dadd}
.ad-disclosure{position:absolute;left:220px;top:366px;width:760px;text-align:center;font-size:11px;line-height:20px;color:#333}
</style>
</head>
<body>

<header class="site-header">
  <div class="brand"><span class="brand-mark"></span>CoinHarbor.com</div>
  <div class="search">Search
    <svg width="14" height="14" viewBox="0 0 14 14"><circle cx="6" cy="6" r="4.5" fill="none" stroke="#333" stroke-width="2"/><line x1="9.5" y1="9.5" x2="13" y2="13" stroke="#333" stroke-width="2"/></svg>
  </div>
</header>

<nav class="main-nav">
  <ul>
    <li class="active" style="width:87px;text-align:center">HOME</li>
    <li style="width:116px;text-align:center">ANNUITIES</li>
    <li style="width:139px;text-align:center">AUTO INSURANCE</li>
    <li style="width:178px;text-align:center">CREDIT MONITORING</li>
    <li style="width:170px;text-align:center">DEBT MANAGEMENT</li>
    <li style="width:126px;text-align:center">MORTGAGES</li>
  </ul>
</nav>

<section class="hero" role="img" aria-label="Business person working on a laptop with financial charts overlaid">
  <h1>Make smarter financial decisions</h1>
  <p class="tagline">FIND THE BEST FINANCIAL PRODUCTS &amp; SERVICES</p>
  <p class="disclosure">Disclosure: We receive advertising revenue from some partners. Learn more.</p>
  <span class="hero-arrow" style="left:28px"><svg width="29" height="29" viewBox="0 0 29 29"><polyline points="17,9 11,14.5 17,20" fill="none" stroke="#fff" stroke-width="1.5"/></svg></span>
  <span class="hero-arrow" style="left:1140px"><svg width="29" height="29" viewBox="0 0 29 29"><polyline points="12,9 18,14.5 12,20" fill="none" stroke="#fff" stroke-width="1.5"/></svg></span>
</section>

<main>
  <div class="finder"><b>I'm looking for</b> <span>Product or categories</span></div>

  <div class="category-grid">
    <div class="category"><div class="thumb" role="img" aria-label="Hands counting coins" style="background:linear-gradient(135deg,#d9c9b5,#8a6f55)"></div><p>Annuities</p></div>
    <div class="category"><div class="thumb" role="img" aria-label="Hands shielding a small car" style="background:linear-gradient(135deg,#2c4160,#0c1524)"></div><p>Auto Insurance</p></div>
    <div class="category"><div class="thumb" role="img" aria-label="Couple checking a credit report on a laptop" style="background:linear-gradient(135deg,#6b4a36,#2a1c14)"></div><p>Credit Monitoring</p></div>
    <div class="category"><div class="thumb" role="img" aria-label="Pen over a credit report form" style="background:linear-gradient(135deg,#e8e0d2,#b98f5a)"></div><p>Credit Repair</p></div>
    <div class="category"><div class="thumb" role="img" aria-label="Person reviewing bills at a desk" style="background:linear-gradient(135deg,#c2a98c,#5d4636)"></div><p>Debt Management</p></div>
    <div class="category"><div class="thumb" role="img" aria-label="Code on a dark screen" style="background:linear-gradient(135deg,#1d3a44,#07151a)"></div><p>Identity Theft</p></div>
    <div class="category"><div class="thumb" role="img" aria-label="Hands protecting paper family figures" style="background:linear-gradient(135deg,#f0d9b6,#c08a4f)"></div><p>Life Insurance</p></div>
    <div class="category"><div class="thumb" role="img" aria-label="Model house held in a hand" style="background:linear-gradient(135deg,#3b4a63,#12161f)"></div><p>Mortgages</p></div>
    <div class="category"><div class="thumb" role="img" aria-label="Glass office towers seen from below" style="background:linear-gradient(135deg,#6d8bb5,#2c4670)"></div><p>Online Brokerages</p></div>
    <div class="category"><div class="thumb" role="img" aria-label="Hands exchanging banknotes" style="background:linear-gradient(135deg,#d8d2c8,#8e8578)"></div><p>Payday Loans</p></div>
    <div class="category"><div class="thumb" role="img" aria-label="Calculator and piggy bank" style="background:linear-gradient(135deg,#9fc9c9,#e6d6cc)"></div><p>Personal Finance</p></div>
    <div class="category"><div class="thumb" role="img" aria-label="Graduate with a laptop" style="background:linear-gradient(135deg,#cfc6bc,#6e5a4c)"></div><p>Student Loan Consolidation</p></div>
    <div class="category"><div class="thumb" role="img" aria-label="Advisors meeting at a table" style="background:linear-gradient(135deg,#7a6a5c,#2c2622)"></div><p>Tax Settlement</p></div>
  </div>

  <aside class="ad-column">
    <div class="ad ad-brand" style="top:583px;height:189px;background:linear-gradient(180deg,#2e4a8a,#1a2850)" role="img" aria-label="CoinHarbor advertisement over a city skyline">COINHARBOR</div>
    <div class="ad" style="top:791px;height:223px;background:linear-gradient(180deg,#c7202c,#e6c63e)" role="img" aria-label="Fizzmere sparkling water advertisement with fruit and bottles"></div>
    <div class="ad" style="top:1024px;height:380px;background:linear-gradient(180deg,#1c1a18,#3a302a)" role="img" aria-label="Stridewell sneaker advertisement with a red sneaker"></div>
  </aside>

  <div class="divider"></div>

  <section class="about">
    <h2>What is CoinHarbor.com?</h2>
    <p class="sub">Financial Service Advice and Reviews</p>
    <div class="features">
      <div class="feature f1">
        <svg width="62" height="54" viewBox="0 0 62 54" fill="none" stroke="#fff" stroke-width="3"><rect x="3" y="3" width="44" height="32" rx="2"/><polyline points="10,26 19,16 27,23 38,11"/><circle cx="44" cy="36" r="9"/><line x1="50" y1="43" x2="58" y2="51"/></svg>
        <h3>We Analyze &amp; Explain</h3>
        <p>We analyze &amp; explain how each online service works</p>
      </div>
      <div class="feature f2">
        <svg width="54" height="54" viewBox="0 0 54 54" fill="none" stroke="#fff" stroke-width="3"><rect x="6" y="4" width="30" height="38" rx="3"/><rect x="20" y="14" width="30" height="36" rx="3" fill="#1567d9"/><polyline points="26,32 33,32 31,28"/><polyline points="44,36 37,36 39,40"/></svg>
        <h3>We Test &amp; Compare</h3>
        <p>We test &amp; compare the leading services in each category</p>
      </div>
      <div class="feature f3">
        <svg width="60" height="54" viewBox="0 0 60 54" fill="#fff"><circle cx="20" cy="13" r="10"/><path d="M2 50c0-13 8-22 18-22s16 6 18 12l-6 10z"/><polygon points="45,24 48.5,32 57,32 50,37 53,46 45,40.5 37,46 40,37 33,32 41.5,32"/></svg>
        <h3>We Review &amp; Rate</h3>
        <p>We review and rate each service to show which is best</p>
      </div>
    </div>
  </section>

  <section class="reviews">
    <svg class="notch" width="60" height="30" viewBox="0 0 60 30"><polygon points="0,0 60,0 30,30" fill="#fff"/></svg>
    <h2>Client Reviews</h2>
    <span class="slide-btn" style="left:164px"><svg width="12" height="16" viewBox="0 0 12 16"><polyline points="9,2 3,8 9,14" fill="none" stroke="#888" stroke-width="2"/></svg></span>
    <div class="avatar" role="img" aria-label="Portrait of a client"></div>
    <p class="quote">“ Lorem ipsum dolor sit amet, consectetur adipiscing elit, sed do eiusmod tempor incididunt ut labore et dolore magna aliqua. Ut enim ad minim veniam, quis nostrud exercitation ullamco laboris nisi ut aliquip ex ea commodo consequat uis aute irure dolor in reprehenderit in voluptate velit esse cillum dolore eu fugiat nulla pariaturoa.”</p>
    <p class="reviewer">Reed Calloway, CEO</p>
    <p class="stars">☆☆☆☆☆</p>
    <span class="slide-btn" style="left:978px"><svg width="12" height="16" viewBox="0 0 12 16"><polyline points="3,2 9,8 3,14" fill="none" stroke="#888" stroke-width="2"/></svg></span>
  </section>

  <section class="articles">
    <h2>Latest Articles</h2>
    <article class="article" style="left:162px;top:2476px">
      <div class="thumb" role="img" aria-label="Businessman holding a rupee symbol" style="background:linear-gradient(135deg,#2f6f8f,#0e2a3a)"></div>
      <h3>5 "Easy" Ways Parents Can Save $1000's a Year</h3>
      <p>Parents, let's face it – the high cost of raising children leaves us all needing a little extra money. Short of getting a big raise, switching jobs, or winning...</p>
      <a href="#">READ MORE...</a>
    </article>
    <article class="article" style="left:462px;top:2476px">
      <div class="thumb" role="img" aria-label="Blue sport motorcycle" style="background:linear-gradient(135deg,#6a6e78,#1b1d24)"></div>
      <h3>Motorcycle Insurance Basics</h3>
      <p>Motorcycle insurance can be quite expensive. It can be the same amount as an auto insurance quote in some cases. Depending on the coverage you select and your driving...</p>
      <a href="#">READ MORE...</a>
    </article>
    <article class="article" style="left:762px;top:2476px">
      <div class="thumb" role="img" aria-label="Hand holding a car key" style="background:linear-gradient(135deg,#9eb07a,#2e3a22)"></div>
      <h3>How Do I Get Cheap Auto Insurance?</h3>
      <p>If you're looking for cheap auto insurance, then you aren't alone. Many drivers regularly search for lower cost, more affordable insurance for their...</p>
      <a href="#">READ MORE...</a>
    </article>
    <article class="article" style="left:162px;top:2822px">
      <div class="thumb" role="img" aria-label="Cars in city traffic" style="background:linear-gradient(135deg,#a8896a,#3a2e26)"></div>
      <h3>LA Car Insurance Requirements</h3>
      <p>If you live in Louisiana you are no doubt aware that you have to carry LA auto insurance in order to legally operate a motor vehicle. However...</p>
      <a href="#">READ MORE...</a>
    </article>
    <article class="article" style="left:462px;top:2822px">
      <div class="thumb" role="img" aria-label="Driver at the wheel of a car" style="background:linear-gradient(135deg,#8a8d92,#2a2b2e)"></div>
      <h3>How Do I Buy General Auto Insurance?</h3>
      <p>Most people already have budgets that are extremely stretched; therefore, it is not surprising that most people want to spend the least amount they...</p>
      <a href="#">READ MORE...</a>
    </article>
    <article class="article" style="left:762px;top:2822px">
      <div class="thumb" role="img" aria-label="Young driver with an instructor in a car" style="background:linear-gradient(135deg,#c9d2dc,#6f7b88)"></div>
      <h3>How to Shop for Young Driver's Insurance?</h3>
      <p>Everyone one needs car insurance, including young drivers...especially young drivers. Auto insurance for young drivers can often be rather expensive...</p>
      <a href="#">READ MORE...</a>
    </article>
  </section>
</main>

<footer class="site-footer">
  <h4 style="left:162px">All Services Reviewed</h4>
  <ul style="left:162px">
    <li>Annuities</li><li>Auto Insurance</li><li>Credit Monitoring</li><li>Credit Repair</li><li>Debt Management</li><li>Homeowners Insurance</li><li>Identity Theft</li><li>&nbsp;Life Insurance</li>
  </ul>
  <ul style="left:349px">
    <li>Mortgages</li><li>Online Brokerages</li><li>Payday Loans</li><li>Personal Finance</li><li>Student Loan Consolidation</li><li>Tax Settlement</li>
  </ul>
  <h4 style="left:574px">Popular Services</h4>
  <ul style="left:574px">
    <li>Debt Management</li><li>Payday Loans</li><li>Credit Cards</li>
  </ul>
  <h4 style="left:766px">Subscribe to our newsletter</h4>
  <p class="news-text">Subscribe to our newsletter to get the latest great deals and reviews</p>
  <div class="email">Email</div>
  <div class="signup">SIGN UP</div>

  <div class="footer-rule"></div>
  <p class="copyright">Copyright © 2017 CoinHarbor. All rights reserved. About us / Privacy Policy / Terms of Service / Contact us</p>
  <div class="social" aria-label="Social links"><span></span><span></span><span></span><span></span></div>
  <div class="footer-rule2"></div>
  <p class="ad-disclosure">Advertising Disclosure: CoinHarbor.com is an independent, advertising-supported comparison service. CoinHarbor.com may be compensated in exchange for featured placement of certain sponsored products and services, or your clicking on links posted on this website.</p>
</footer>

</body>
</html>
```